Business card for a new innovative and professional lawn care business

We need a business card design for a new lawn care business in Halifax NS Canada. We offer lawn services in Halifax & Bedford. Our services offered include lawn care, garden services, and property maintenance. We take pride in our work and are experienced at what we do. I would like to see a design that is double sided. On the backside I would like the something simple (maybe my logo preferably on blackround (linked below) with website link, Facebook page or something). The front I want to include contact info:
Morgan Pell
phone 902-555-0148
email - brookvaleyards.ca
facebook - Leafnet.com/brookvaleyards
Instagram maybe ? - greenpix.com/brookvaleyard
Serving Halifax and Bedford for 5 years?
I don't want it to have too much information as I will be passing them out in aim to visit website, or call !
We do want it to include lawn care, garden services and property maintenance.
Basic, catchy, and modern looking !
Logo attached below !

Target Market(s)

Passing business cards to everyone I meet or interact with.

Industry/Entity Type

Lawn Care

Contact Information for Business Card

Double sided with some basic information, with catchy colours and easy to look at.

Font styles to use
Sans Serif

Requirements
Must have
• Must be double sided and have :
• Name, Phone, Email, FB, Website, and 3 main services offered - lawn care, property maintenance, garden services
Nice to have
• Would be nice to have instagram link if it goes well on there
Should not have
• Don't want too much writing or images that are distracting

```html
<!DOCTYPE html>
<html lang="en">
<head>
<meta charset="utf-8">
<title>Brookvale Yards – Business Card</title>
<link href="https://fonts.googleapis.com/css2?family=Open+Sans:wght@400;600;700;800&display=swap" rel="stylesheet">
<style>
  :root {
    --bg: #2e2f31;
    --card: #ffffff;
    --green-dark: #1d8a3b;
    --green-light: #7cc242;
    --mist: #e4ebe6;
    --ink: #222a24;
  }
  * { box-sizing: border-box; margin: 0; padding: 0; }
  html, body { width: 1200px; height: 900px; overflow: hidden; }
  body {
    background: var(--bg);
    font-family: "Open Sans", Arial, sans-serif;
    position: relative;
  }
  .card {
    position: absolute;
    left: 280px;
    width: 640px;
    height: 366px;
    background: var(--card);
    border-radius: 20px;
    overflow: hidden;
  }
  .card--back { top: 48px; }
  .card--front { top: 486px; }
  .card__shapes { position: absolute; inset: 0; }

  .brand {
    position: absolute;
    display: flex;
    align-items: center;
    gap: 12px;
    color: var(--green-dark);
    font-weight: 800;
    letter-spacing: 1px;
    white-space: nowrap;
  }
  .brand__dot {
    width: 22px; height: 22px; border-radius: 50%;
    background: var(--green-light);
    flex: none;
  }
  .card--back .brand { left: 70px; top: 130px; font-size: 40px; }
  .card--front .brand { left: 40px; top: 56px; font-size: 30px; }
  .card--front .brand__dot { width: 18px; height: 18px; }

  .socials {
    position: absolute;
    right: 48px; top: 212px;
    list-style: none;
    font-size: 15px;
    font-weight: 600;
    color: var(--ink);
  }
  .socials li { display: flex; align-items: center; gap: 8px; margin-bottom: 4px; }
  .socials__mark {
    width: 14px; height: 14px; border-radius: 2px;
    background: var(--green-dark);
  }

  .mower-art {
    position: absolute;
    left: 330px; top: 0;
    width: 230px; height: 366px;
    background: linear-gradient(180deg, rgba(228,235,230,0.9), rgba(228,235,230,0.6));
    border-radius: 40px 40px 0 0;
  }

  .services {
    position: absolute;
    right: 52px; top: 80px;
    text-align: right;
    list-style: none;
    color: var(--green-dark);
    font-size: 15px;
    line-height: 1.25;
  }
  .services__title {
    color: var(--green-light);
    font-weight: 700;
    font-size: 17px;
    letter-spacing: 0.5px;
  }
  .services li:not(.services__title)::after {
    content: "";
    display: inline-block;
    width: 7px; height: 7px;
    border-radius: 50%;
    background: var(--green-light);
    margin-left: 8px;
    vertical-align: middle;
  }

  .person { position: absolute; left: 40px; top: 214px; }
  .person__name {
    color: var(--green-light);
    font-weight: 700;
    font-size: 27px;
    letter-spacing: 0.5px;
    line-height: 1.1;
    margin-bottom: 6px;
  }
  .contact { list-style: none; color: var(--green-dark); font-size: 16px; line-height: 1.3; }
  .contact li { display: flex; align-items: center; gap: 8px; }
  .contact svg { width: 12px; height: 12px; flex: none; }
</style>
</head>
<body>

  <section class="card card--back" aria-label="Card back">
    <svg class="card__shapes" viewBox="0 0 640 366" aria-hidden="true">
      <polygon points="250,318 640,300 640,312 262,330" fill="var(--green-light)"/>
      <polygon points="0,302 230,284 268,330 640,312 640,366 0,366" fill="var(--green-dark)"/>
    </svg>
    <div class="brand"><span class="brand__dot"></span>BROOKVALE YARDS</div>
    <ul class="socials">
      <li><span class="socials__mark"></span>Leafnet.com/brookvaleyards</li>
      <li><span class="socials__mark"></span>greenpix.com/brookvaleyard</li>
    </ul>
  </section>

  <section class="card card--front" aria-label="Card front">
    <div class="mower-art" role="img" aria-label="Faint lawn mower illustration in pale grey-green"></div>
    <svg class="card__shapes" viewBox="0 0 640 366" aria-hidden="true">
      <line x1="40" y1="214" x2="560" y2="168" stroke="var(--green-dark)" stroke-width="1.5"/>
      <polygon points="560,168 640,160 640,236 540,246" fill="var(--green-dark)"/>
      <path d="M0,344 Q320,330 640,262 L640,282 Q320,352 0,358 Z" fill="var(--green-light)"/>
    </svg>
    <div class="brand"><span class="brand__dot"></span>BROOKVALE YARDS</div>
    <ul class="services">
      <li class="services__title">SERVICES</li>
      <li>Lawn care</li>
      <li>Garden services</li>
      <li>Property maintenance</li>
    </ul>
    <div class="person">
      <p class="person__name">MORGAN PELL</p>
      <ul class="contact">
        <li><svg viewBox="0 0 12 12"><path d="M2.5 1l2 2.5-1 1.2a7 7 0 0 0 3.8 3.8l1.2-1 2.5 2-1.2 1.5C5.5 11 1 6.5 1 2.2z" fill="var(--green-light)"/></svg>902-555-0148</li>
        <li><svg viewBox="0 0 12 12"><rect x="1" y="2.5" width="10" height="7" rx="1" fill="none" stroke="var(--green-light)" stroke-width="1.3"/><path d="M1.5 3l4.5 3.5L10.5 3" fill="none" stroke="var(--green-light)" stroke-width="1.3"/></svg>info@brookvaleyards.ca</li>
        <li><svg viewBox="0 0 12 12"><circle cx="6" cy="6" r="5" fill="none" stroke="var(--green-light)" stroke-width="1.3"/><path d="M1 6h10M6 1c-2.5 2.8-2.5 7.2 0 10M6 1c2.5 2.8 2.5 7.2 0 10" fill="none" stroke="var(--green-light)" stroke-width="1"/></svg>www.brookvaleyards.ca</li>
      </ul>
    </div>
  </section>

</body>
</html>
```